Business Card - high end, modern health care

Hey designers!

We need a double sided business card for the boutique, cutting edge physical therapy rehabilitation centre in Sydney's Northern Beaches.

With the most qualified physios in the area The Harbourview Motion Clinic does what other physiotherapy practices do not, we take our time with our patients giving them longer appointments, better physios and therefor faster results!

We guarantee that the service people receive at THMC will be unparalleled.

Hence we need a business card to reflect our modern, boutique, high end service. The final design needs to reflect that we are in a class of our own yet with the feel of beachside retreat.

Below I have attached our logo in both blue on white and white on blue. The exact colour is;
and the font that we have used in our logo is Tex Gyre Aventador.

I like the idea of the blue as the main colour as it is more eye catching and our signage onto the main road will be in this blue and in the interest of consistency across marketing the blue needs to be a part of the design. However I would appreciate a few designs onto a wooden background as this is a visual theme within the fitout of the practice.

The design needs to be of standard size (91x55mm).

Target Market(s)

We target people who have an end outcome in mind and those who have had poor experiences with other providers and ensure that everyone gets the care that they deserve with a premium service that is tailored to the individuals circumstances. As a premium service, the target market is highly educated, business and tech savvy with the additional target market of elderly people who have self funded their retirement and see value in paying for the best ongoing rehabilitation to maintain independence.

Industry/Entity Type

Physical Therapy

Contact Information for Business Card

Name, designation( Titled Musculoskeletal Physiotherapist... there will also be those in the company that have multiple designations ie 5 or 6 words long), phone number, email, facebook, instagram, address

Font styles to use
Sans Serif

Colors

Designer to choose colors to be used in the design.

Requirements
Must have
• Front - The logo as large as possible, blue or wooden theme, and all of the important details.
• Back - A blank space/lines on which to write appointment times (no "Appointment, date, time" etc.)
Nice to have
• facebook url
• logos for facebook and instagram
• Mini logos for the phone and email?

```html
<!DOCTYPE html>
<html lang="en">
<head>
<meta charset="utf-8">
<title>The Harbourview Motion Clinic – Business Card</title>
<link href="https://fonts.googleapis.com/css2?family=Montserrat:wght@300;400;700&family=Kaushan+Script&display=swap" rel="stylesheet">
<style>
  :root {
    --backdrop: #d8dbdb;
    --card-white: #ffffff;
    --brand-blue: #1f5bb1;
    --label-blue: #3f66c2;
    --landmark-tint: #a9b0de;
    --wood-dark: #3a2414;
    --wood-mid: #5a3a22;
    --wood-light: #6e4a2c;
    --rule-grey: #d9dbe0;
    --ink: #111111;
  }
  * { box-sizing: border-box; margin: 0; padding: 0; }
  html, body {
    width: 1200px; height: 1000px; overflow: hidden;
    background: var(--backdrop);
    font-family: "Montserrat", sans-serif;
  }
  .card-sheet {
    width: 1200px; height: 1000px;
    display: flex; flex-direction: column; align-items: center; justify-content: center;
    gap: 32px;
  }
  .card {
    position: relative;
    width: 760px; height: 459px;
    border-radius: 34px;
    overflow: hidden;
    box-shadow: 0 6px 18px rgba(0,0,0,.18);
  }

  /* Front – wood-toned surface */
  .card--front {
    background: linear-gradient(100deg, var(--wood-dark), var(--wood-mid) 35%, var(--wood-light) 60%, var(--wood-mid) 85%, var(--wood-dark));
  }
  .front-brand {
    position: absolute; left: 62px; top: 170px;
    display: flex; align-items: center; gap: 22px;
    color: var(--card-white);
  }
  .brand-dot {
    width: 104px; height: 104px; border-radius: 50%;
    background: var(--card-white); flex: none;
  }
  .front-brand .brand-name {
    font-weight: 700; font-size: 44px; line-height: 1.05; letter-spacing: 1px;
    text-transform: uppercase;
  }

  /* Back – details */
  .card--back { background: var(--card-white); }
  .back-brand {
    position: absolute; right: 44px; top: 34px;
    display: flex; align-items: center; gap: 10px;
    color: var(--brand-blue);
  }
  .back-brand .brand-dot { width: 38px; height: 38px; background: var(--brand-blue); }
  .back-brand .brand-name {
    font-weight: 700; font-size: 17px; line-height: 1.1; text-transform: uppercase;
  }
  .write-line {
    position: absolute; left: 110px; right: 44px; height: 1px; background: var(--rule-grey);
  }
  .write-line--1 { top: 98px; }
  .write-line--2 { top: 150px; }
  .write-line--3 { top: 330px; right: 340px; }

  .detail-row {
    position: absolute; left: 58px; display: flex; align-items: baseline;
  }
  .detail-row--name { top: 230px; }
  .detail-row--role { top: 262px; }
  .detail-label {
    width: 140px; color: var(--label-blue); font-weight: 300; font-size: 20px;
  }
  .detail-value {
    font-family: "Kaushan Script", cursive; color: var(--ink); font-size: 24px; line-height: 1.2;
  }
  .detail-row--role .detail-value { width: 220px; }

  .landmark-art {
    position: absolute; left: 430px; top: 170px; width: 300px; height: 170px;
    background: linear-gradient(180deg, rgba(169,176,222,.55), var(--landmark-tint));
    border-radius: 6px;
  }

  .contact-row {
    position: absolute; left: 58px; right: 44px; bottom: 36px;
    display: flex; align-items: center; justify-content: space-between;
    color: var(--brand-blue); font-size: 19px; font-weight: 400;
  }
  .social-handle { display: flex; align-items: center; gap: 8px; }
  .social-dot {
    width: 24px; height: 24px; border-radius: 50%; border: 2px solid var(--brand-blue);
  }
  .base-band {
    position: absolute; left: 0; right: 0; bottom: 0; height: 16px; background: var(--brand-blue);
  }
</style>
</head>
<body>
<main class="card-sheet">
  <section class="card card--front" role="img" aria-label="Dark wooden plank background with the clinic name">
    <div class="front-brand">
      <span class="brand-dot"></span>
      <span class="brand-name">The Harbourview<br>Motion Clinic</span>
    </div>
  </section>

  <section class="card card--back">
    <div class="back-brand">
      <span class="brand-dot"></span>
      <span class="brand-name">The Harbourview<br>Motion Clinic</span>
    </div>

    <span class="write-line write-line--1"></span>
    <span class="write-line write-line--2"></span>

    <div class="landmark-art" role="img" aria-label="Soft blue line illustration of a harbourside building with a boat"></div>

    <div class="detail-row detail-row--name">
      <span class="detail-label">Name:</span>
      <span class="detail-value">Alex Marlow</span>
    </div>
    <div class="detail-row detail-row--role">
      <span class="detail-label">Designation:</span>
      <span class="detail-value">Titled Musculoskeletal Physiotherapist</span>
    </div>
    <span class="write-line write-line--3"></span>

    <div class="contact-row">
      <span class="contact-email">email@example.com</span>
      <span class="social-handle"><span class="social-dot"></span>@examplename</span>
      <span class="social-handle"><span class="social-dot"></span>@examplename</span>
    </div>
    <span class="base-band"></span>
  </section>
</main>
</body>
</html>
```